Im want a website LIKE VRX's and FleetHollow.com's with product payment options like Trenzo's

I need a website LIKE VRX with a header made EXACTLY LIKE THAT OF FLEETHOLLOWS .

The front page photo should be like that of FLEETHOLLOW's webpage as well.

The name of the website will be called "M.K. (Caldera Key)".

We will be targeting ALL MARKETS in a small town in central Panama and charging businesses "listing fees" like a phone book does but also providing informational blogs, news, and other interesting activities.

THIS IS A MULTI PAGE WEBSITE

THIS IS WHERE VRX's website meets Brivelle/FleetHollow.

Once the layout is built I will tweak and modify, add information, and upload items for sale.

Here is a list of specific categories that should be listed out above the front page header image/search bar

-- Home -- News -- Travel -- Activities -- Shop & Dine -- Store -- More... --

These categories should be spread across the bottom of the page in three sections:

WHATS SO GREAT ABOUT (Caldera Key),
HAND PICKED TOURS
ACTIVITIES etc.

Also lets use www.Trenzo.example 's
"HOT DESTINATIONS"
"BEAT THE BEST PRICES IN BOQUETE"
"OCTOBERS INSIDER PICKS"
"TOP DESTINATIONS"
and spread them in four sections side-by-side near the bottom of the page.

Overall I would like to see the finished product to be something LIKE VRX's and FleetHollows.

WE NEED ONLINE PAYMENT OPTIONS LIKE BRIVELLE'S WEBSITE HAS

This will be a desktop website but should be very mobile friendly as well.

-rodmund

P.S. Good luck!

If it isn't already too late to change the website name, the name of the website should be "Caldera Key". Added Friday, October 9, 2015

What do you guys think the budget should be to win this? Added Saturday, October 10, 2015

www.palmorra.example is the most amazing simple site. Whoever can make me a replica with my specifications will win immediately!!!! Added Sunday, October 18, 2015

OMG www.palmorra.example is the bomb!So simple and elegant. Whoever can make me an EXACT REPLICA OF WWW.PALMORRA.EXAMPLE as my site with the specifications mentioned in my brief will take home the $825.00 immediately! Good luck amigos! Added Sunday, October 18, 2015

Does anybody know how to add recurring monthly billing options on this website? Added Sunday, October 18, 2015

ALL MARKETS

Product

Coded - Design and coding required

5+ page

• Coinvey payment options.
• I must be able to add and remove photos/text and video from the HTML files in the page.
• Be creative my friends, and may the odds be forever in your favor!
• I added some photos of a good layout for our page below.

```html
<!DOCTYPE html>
<html lang="en">
<head>
<meta charset="utf-8">
<title>Contact — Caldera Key</title>
<link rel="stylesheet" href="https://fonts.googleapis.com/css2?family=Open+Sans:wght@400;600;700&family=Lato:wght@300;400;700&display=swap">
<style>
:root{
  --teal:#1fa3b8;
  --teal-dark:#178a9c;
  --ink:#2f2f2f;
  --muted:#7d7d7d;
  --line:#d9d9d9;
  --header:#23262a;
  --footer:#2b2e33;
  --footer-deep:#1f2226;
  --footer-text:#9aa0a6;
  --promo-blue:#2f7fd1;
  --promo-red:#e2463a;
  --white:#ffffff;
}
*{box-sizing:border-box;margin:0;padding:0}
html,body{width:865px;height:1200px;overflow:hidden}
body{font-family:"Open Sans",Arial,sans-serif;color:var(--ink);background:var(--white);position:relative;font-size:10px}

/* header */
.site-header{position:absolute;left:0;top:0;width:865px;height:64px;background:var(--header)}
.topline{position:absolute;right:38px;top:6px;display:flex;gap:12px;font-size:7.5px;color:#c9ced3}
.topline span{display:flex;align-items:center;gap:4px}
.brand{position:absolute;left:38px;top:30px;font-family:"Lato",sans-serif;font-weight:400;font-size:22px;color:var(--teal);letter-spacing:.3px}
.main-nav{position:absolute;right:38px;top:24px;display:flex;height:40px}
.main-nav a{display:flex;align-items:center;padding:0 12px;color:var(--white);font-size:8.5px;font-weight:600;text-decoration:none;letter-spacing:.4px}
.main-nav a.current{background:var(--teal)}

/* page banner */
.page-banner{position:absolute;left:0;top:64px;width:865px;height:94px;background:linear-gradient(90deg,var(--teal-dark),var(--teal))}
.page-banner h1{position:absolute;left:38px;top:16px;font-family:"Lato",sans-serif;font-weight:400;font-size:30px;color:var(--white)}
.page-banner p{position:absolute;left:38px;top:56px;font-size:9px;color:#dff3f6}

/* contact form column */
.contact-main{position:absolute;left:38px;top:200px;width:500px}
.section-title{font-family:"Lato",sans-serif;font-weight:700;font-size:12px;color:var(--ink)}
.social-row{display:flex;gap:6px;margin-top:12px}
.social-row i{display:block;width:17px;height:17px;border-radius:50%}
.form-title{margin-top:26px;font-family:"Lato",sans-serif;font-weight:700;font-size:12px}
.form-intro{margin-top:8px;font-size:8px;line-height:12px;color:var(--muted);width:490px}
.field{margin-top:22px}
.field label{display:block;font-size:8.5px;color:var(--ink);margin-bottom:8px}
.field .input{width:320px;height:20px;border:1px solid var(--line)}
.field .textarea{width:490px;height:124px;border:1px solid var(--line)}
.submit{display:inline-block;margin-top:14px;background:var(--teal);color:var(--white);font-size:9px;font-weight:600;padding:6px 13px;border-radius:2px}

/* sidebar */
.sidebar{position:absolute;left:547px;top:200px;width:283px}
.sidebar .section-title{text-transform:uppercase;letter-spacing:.4px}
.map{margin-top:14px;width:203px;height:144px;background:linear-gradient(135deg,#e6ece0,#cfdde9);border:1px solid var(--line)}
.rule{height:1px;background:var(--line);margin-top:14px}
.sidebar .info-title{margin-top:10px}
.info-block{margin-top:14px;font-size:7.5px;line-height:12px;color:var(--muted);border-bottom:1px solid var(--line);padding-bottom:12px}
.info-block b{color:var(--ink);font-weight:600}

/* tweet band */
.tweet-band{position:absolute;left:0;top:743px;width:865px;height:92px;background:var(--teal)}
.tweet-band .bird{position:absolute;left:38px;top:32px}
.tweet-band p{position:absolute;left:92px;top:38px;font-size:8px;color:var(--white);width:700px}
.tweet-band p b{font-weight:700}

/* footer */
.site-footer{position:absolute;left:0;top:835px;width:865px;height:317px;background:var(--footer)}
.footer-about{position:absolute;left:38px;top:40px;width:250px}
.footer-about .brand-foot{font-family:"Lato",sans-serif;font-size:20px;color:var(--teal)}
.footer-about p{margin-top:12px;font-size:7.5px;line-height:11.5px;color:var(--footer-text)}
.badges{display:flex;gap:12px;margin-top:22px}
.badges span{display:block;width:48px;height:26px;border-radius:13px;background:#464a50}
.deals{position:absolute;left:337px;top:40px;width:190px}
.deals h3{font-family:"Lato",sans-serif;font-size:12px;color:var(--teal);font-weight:700;text-transform:uppercase;letter-spacing:.4px}
.deal{display:flex;gap:10px;margin-top:16px}
.deal .thumb{width:44px;height:40px;border-radius:2px;flex:none}
.deal h4{font-size:9px;color:var(--white);font-weight:600}
.deal small{display:block;margin-top:5px;font-size:7px;color:var(--footer-text)}
.deal small em{font-style:normal;color:#f2b632;margin-right:6px}
.promo{position:absolute;left:553px;width:190px;border-radius:3px;text-align:center;color:var(--white);padding-top:22px}
.promo.blue{top:38px;height:107px;background:linear-gradient(180deg,#3a8fe0,var(--promo-blue))}
.promo.red{top:165px;height:115px;background:linear-gradient(180deg,#ea5a45,var(--promo-red))}
.promo strong{display:block;font-family:"Lato",sans-serif;font-weight:300;font-size:28px}
.promo span{display:block;margin-top:6px;font-size:12px}
.promo .line{display:block;width:150px;height:1px;background:rgba(255,255,255,.5);margin:10px auto 0}
.copyright{position:absolute;left:0;top:1152px;width:865px;height:48px;background:var(--footer-deep);text-align:center;font-size:8px;color:var(--footer-text);line-height:48px}
.copyright b{color:var(--white);font-weight:600}
</style>
</head>
<body>

<header class="site-header">
  <div class="topline">
    <span><svg width="8" height="6" viewBox="0 0 8 6"><rect x=".5" y=".5" width="7" height="5" fill="none" stroke="#c9ced3"/><path d="M.5 .5 4 3.5 7.5 .5" fill="none" stroke="#c9ced3"/></svg>hello@calderakey.example</span>
    <span><svg width="7" height="7" viewBox="0 0 7 7"><path d="M1 1c0 3 2 5 5 5l.5-1.5-1.5-1-1 1C3 4 3 4 2.5 3l1-1L2.5.5z" fill="#c9ced3"/></svg>+507 555 0142</span>
  </div>
  <div class="brand">Caldera Key</div>
  <nav class="main-nav">
    <a href="#">HOME</a><a href="#">PAGES</a><a href="#">PACKAGE</a><a href="#">LOCATIONS</a><a href="#">BLOG</a><a href="#">SHORTCODES</a><a href="#" class="current">CONTACT</a>
  </nav>
</header>

<section class="page-banner">
  <h1>Contact</h1>
  <p>Pellentesque habitant morbi tristique senectus</p>
</section>

<main class="contact-main">
  <h2 class="section-title">Social Network</h2>
  <div class="social-row">
    <i style="background:#3b5998"></i><i style="background:#29a9e1"></i><i style="background:#dd4b39"></i><i style="background:#cb2027"></i><i style="background:#0e76a8"></i><i style="background:#f7941d"></i><i style="background:#5b9a68"></i><i style="background:#ea4c89"></i>
  </div>
  <h2 class="form-title">Please full fill this form or Using information on the right</h2>
  <p class="form-intro">Sed ut perspiciatis unde omnis iste natus error sit voluptatem accusantium doloremque laudantium, totam rem aperiam, eaque ipsa quae ab illo inventore veritatis et quasi architecto beatae vitae dicta sunt explicabo. Nemo enim ipsam voluptatem quia voluptas sit aspernatur aut odit aut fugit, sed quia consequuntur magni dolores eos qui ratione voluptatem sequi nesciunt.</p>
  <div class="field"><label>Name *</label><div class="input"></div></div>
  <div class="field"><label>Email *</label><div class="input"></div></div>
  <div class="field"><label>Message *</label><div class="textarea"></div></div>
  <span class="submit">Submit</span>
</main>

<aside class="sidebar">
  <h2 class="section-title">Our Map</h2>
  <div class="map" role="img" aria-label="Street map showing the office location"></div>
  <div class="rule"></div>
  <h2 class="section-title info-title">Contact Information</h2>
  <div class="info-block"><b>Calle Norte:</b> 12 Avenida del Río, Alto Valle, Chiriquí<br>+507 555 0142 &nbsp; hello@calderakey.example<br>Open Monday to Saturday, 8am – 6pm</div>
  <div class="info-block"><b>Plaza Central:</b> 4 Camino Viejo, Bajo Mono<br>+507 555 0187 &nbsp; tours@calderakey.example</div>
</aside>

<section class="tweet-band">
  <svg class="bird" width="28" height="28" viewBox="0 0 28 28"><circle cx="14" cy="14" r="13" fill="#ffffff"/></svg>
  <p><b>RT @calderakey:</b> "Planning a trip to the highlands? Our guide to coffee farms and waterfalls is live." – visit calderakey.example/blog</p>
</section>

<footer class="site-footer">
  <div class="footer-about">
    <div class="brand-foot">Caldera Key</div>
    <p>Fusce vel dui vitae turpis cursus elementum. Integer ornare dictum ligula, in mattis lorem luctus quis. Praesent quis ex non nisi lacinia porta. Donec id diam sed ipsum viverra tempor sit amet vel mi. Nam at lacus nec ante semper.</p>
    <div class="badges"><span></span><span></span><span></span></div>
  </div>

  <div class="deals">
    <h3>Last Minute Deals</h3>
    <div class="deal"><div class="thumb" role="img" aria-label="City skyline photo" style="background:linear-gradient(135deg,#c89a5c,#6d5a48)"></div><div><h4>Rome, Milan, Madrid</h4><small><em>★★★★</em>$1,240 · 7 days</small></div></div>
    <div class="deal"><div class="thumb" role="img" aria-label="Historic square photo" style="background:linear-gradient(135deg,#d6b58a,#8c6a4a)"></div><div><h4>Rome City Tour</h4><small><em>★★★★</em>$690 · 4 days</small></div></div>
    <div class="deal"><div class="thumb" role="img" aria-label="Bay bridge photo" style="background:linear-gradient(135deg,#7fa7c8,#3f5f7d)"></div><div><h4>San Francisco</h4><small><em>★★★★</em>$980 · 5 days</small></div></div>
    <div class="deal"><div class="thumb" role="img" aria-label="Savanna wildlife photo" style="background:linear-gradient(135deg,#b9a25a,#5e6b3a)"></div><div><h4>Wild Life Tour</h4><small><em>★★★★</em>$1,450 · 9 days</small></div></div>
  </div>

  <div class="promo blue" role="img" aria-label="European city travel offer"><strong>20% Off</strong><i class="line"></i><span>Rome, Milan, Madrid</span></div>
  <div class="promo red" role="img" aria-label="San Francisco travel offer"><strong>30% Off</strong><i class="line"></i><span>San Francisco</span></div>
</footer>

<div class="copyright">Copyright © 2015 All Right Reserved. <b>Caldera Key</b></div>

</body>
</html>
```